Meridale Real Estate

We are looking for help with web design for a new company that is revolutionizing the real estate world on the listing side: by charing per hour for top level professional real estate services. We would like the concept to be simple, clean and easily understood.
Updates

We want this website to actually function, not just a static design.

Industry/Entity Type

Real Estate

```html
<!DOCTYPE html>
<html lang="en">
<head>
<meta charset="utf-8">
<title>Meridale Real Estate</title>
<link rel="stylesheet" href="https://fonts.googleapis.com/css2?family=Open+Sans:ital,wght@0,300;0,400;0,600;1,400&display=swap">
<style>
  :root {
    --maroon-dark: #6f1d21;
    --maroon: #8a2c30;
    --maroon-light: #9a3a3d;
    --tan-light: #f6dcab;
    --tan-dark: #d8aa66;
    --nav-text: #5e1a1a;
    --cream: #f1e3c4;
    --gold: #d3a04c;
    --ink: #333333;
    --body-text: #5a5a5a;
    --rule: #dddddd;
    --white: #ffffff;
  }
  html, body { margin: 0; padding: 0; overflow: hidden; background: var(--white); }
  .page {
    position: relative; width: 930px; height: 1200px; overflow: hidden;
    font-family: "Open Sans", Arial, sans-serif; color: var(--ink); background: var(--white);
  }
  .topbar {
    position: absolute; left: 0; top: 0; width: 930px; height: 98px;
    background: linear-gradient(180deg, var(--maroon-light) 0%, var(--maroon) 40%, var(--maroon-dark) 100%);
    border-top: 4px solid #b56a6a; box-sizing: border-box;
  }
  .call { position: absolute; right: 56px; top: 38px; text-align: right; color: var(--white); }
  .call-label { font-size: 13px; letter-spacing: 0.3px; }
  .call-number { font-size: 21px; margin-top: 2px; }
  .nav {
    position: absolute; left: 0; top: 98px; width: 930px; height: 47px;
    background: linear-gradient(180deg, var(--tan-light) 0%, #efca8c 55%, var(--tan-dark) 100%);
  }
  .nav a {
    position: absolute; top: 0; height: 47px; line-height: 47px;
    font-size: 14.5px; color: var(--nav-text); text-decoration: none;
  }
  .nav .sep { position: absolute; top: 0; width: 1px; height: 47px; background: #c49558; }
  .logo {
    position: absolute; left: 372px; top: 17px; width: 176px; height: 176px;
    border-radius: 50%; background: var(--maroon); border: 6px solid var(--cream);
    display: flex; align-items: center; justify-content: center; z-index: 3;
  }
  .logo-name {
    color: var(--cream); font-size: 16px; font-weight: 400; text-transform: uppercase;
    letter-spacing: 3px; text-align: center; line-height: 1.6; width: 130px;
  }
  .hero {
    position: absolute; left: 0; top: 145px; width: 930px; height: 354px;
    background: linear-gradient(100deg, #8c8b7c 0%, #ddd6c6 22%, #e9e1d0 45%, #b9a88e 62%, #ece5d6 82%, #cfc5b3 100%);
  }
  .hero-shade {
    position: absolute; left: 0; bottom: 0; width: 930px; height: 120px;
    background: linear-gradient(180deg, rgba(80,70,55,0) 0%, rgba(80,70,55,0.45) 100%);
  }
  .hero-title {
    position: absolute; left: 0; top: 128px; width: 930px; text-align: center;
    color: var(--white); text-shadow: 0 1px 4px rgba(0,0,0,0.45);
  }
  .hero-title .line1 { font-size: 32px; font-weight: 600; letter-spacing: 0.2px; }
  .hero-title .line2 { font-size: 25px; font-weight: 600; margin-top: 0; }
  .hero-arrow { position: absolute; top: 128px; }
  .about { position: absolute; left: 57px; top: 526px; width: 818px; }
  .about h1 { margin: 0; font-size: 29px; font-weight: 300; color: var(--ink); }
  .about .lead { margin: 10px 0 4px; font-size: 14.5px; color: var(--ink); }
  .about p { margin: 0 0 10px; font-size: 10.6px; line-height: 17.6px; color: var(--body-text); }
  .divider { position: absolute; left: 52px; top: 790px; width: 828px; height: 1px; background: var(--rule); }
  .reviews-title {
    position: absolute; left: 54px; top: 824px; margin: 0;
    font-size: 23px; font-weight: 400; color: var(--maroon-dark);
  }
  .review { position: absolute; width: 215px; }
  .review q { display: block; font-style: italic; font-size: 10.5px; line-height: 18px; color: var(--body-text); quotes: none; }
  .review .author { margin-top: 4px; font-size: 12.5px; color: var(--ink); }
  .portfolio-title {
    position: absolute; left: 550px; top: 824px; margin: 0;
    font-size: 23px; font-weight: 400; color: var(--gold);
  }
  .thumb { position: absolute; width: 101px; height: 85px; border: 1px solid #e0e0e0; }
  .footer {
    position: absolute; left: 0; top: 1103px; width: 930px; height: 97px;
    background: linear-gradient(180deg, var(--maroon) 0%, var(--maroon-dark) 100%);
  }
  .footer-links { position: absolute; left: 53px; top: 24px; font-size: 12.5px; color: var(--white); }
  .footer-links a { color: var(--white); text-decoration: none; }
  .footer-links .bar { margin: 0 6px; }
  .copyright { position: absolute; left: 53px; top: 50px; font-size: 6.5px; font-weight: 600; color: var(--white); }
  .social { position: absolute; right: 56px; top: 28px; display: flex; gap: 8px; }
  .social span { display: block; width: 20px; height: 20px; border-radius: 50%; background: var(--white); }
</style>
</head>
<body>
<div class="page">

  <header class="topbar">
    <div class="call">
      <div class="call-label">CALL US NOW</div>
      <div class="call-number">555 014 2290</div>
    </div>
  </header>

  <nav class="nav">
    <a href="#" style="left:96px">HOME</a>
    <span class="sep" style="left:154px"></span>
    <a href="#" style="left:172px">ABOUT US</a>
    <span class="sep" style="left:258px"></span>
    <a href="#" style="left:276px">PORTFOLIO</a>
    <a href="#" style="left:580px">SERVICES</a>
    <span class="sep" style="left:661px"></span>
    <a href="#" style="left:679px">TESTIMONIALS</a>
    <span class="sep" style="left:796px"></span>
    <a href="#" style="left:813px">CONTACT</a>
  </nav>

  <div class="logo">
    <div class="logo-name">Meridale Real Estate</div>
  </div>

  <section class="hero" role="img" aria-label="Photo of a bright modern kitchen with white cabinets, range and dining area">
    <div class="hero-shade"></div>
    <div class="hero-title">
      <div class="line1">CONSTRUCTION KITCHEN &amp; BATH DESIGN</div>
      <div class="line2">COMMERCIAL &amp; RESIDENTIAL</div>
    </div>
    <svg class="hero-arrow" style="left:18px" width="30" height="70" viewBox="0 0 30 70">
      <polyline points="28,2 2,35 28,68" fill="none" stroke="#222" stroke-width="1.5"/>
    </svg>
    <svg class="hero-arrow" style="left:876px" width="30" height="70" viewBox="0 0 30 70">
      <polyline points="2,2 28,35 2,68" fill="none" stroke="#222" stroke-width="1.5"/>
    </svg>
  </section>

  <section class="about">
    <h1>Background Experience</h1>
    <div class="lead">Etiam eu urna Sed porta Suspendisse quam leo molestie sed luctus quis feugiat in pede Fusce tellus Sed metus augue</div>
    <p>ut pulvinar eu ante Integer orci tellus tristique vitae consequat nec porta vel lectus Nulla sit amet diam Duis non nunclibero a tempus libero lectus feugiat felis Morbi diam mauris viverra in gravida eu mattis in ante Morbi eget arcu Morbi porta libero id ullamcorper nonummy nibh ligula pulvinar metus eget consv et scelerisque</p>
    <p>Pellentesque faucibus Ut accumsan ultricies elit Maecenas at justo id velit placerat molestie Donec dictum lectus non odio Cras a ante vitae enim iaculis aliquam Mauris nunc quam venenatis nec euismod sit amet egestas placerat est Pellentesque habitant morbi tristique senectus et netus et malesuada fames ac turpis egestas Cras id elit Integer quis urna Ut ante enim dapibus malesuada fringilla eu condimentum quis tellus Aenean porttitor eros vel dolor Donec convallis pede venenatis nibh Duis quam Nam eget lacus Aliquam erat volutpat Quisque dignissim congue leo</p>
    <p>Mauris vel lacus vitae felis vestibulum volutpat Etiam est nunc venenatis in tristique eu imperdiet ac nisl Cum sociis natoque penatibus et magnis dis parturient montes nascetur ridiculus mus In iaculis facilisis massa Etiam eu urna Sed porta Suspendisse quam leo molestie sed luctus quis feugiat in pede Fusce tellus</p>
  </section>

  <div class="divider"></div>

  <h2 class="reviews-title">Customer Reviews</h2>
  <div class="review" style="left:56px; top:864px">
    <q>Est nunc venenatis in tristique eu imperdiet ac nisl Cum sociis natoque penatibus et magnis dis parturient montes nascetur ridiculus mus In iaculis facilisis massa Etiam</q>
    <div class="author">By Author Name</div>
  </div>
  <div class="review" style="left:295px; top:864px">
    <q>Nunc venenatis in tristique eu imperdiet ac nisl Cum sociis natoque penatibus et magnis dis parturient montes nascetur ridiculus mus In iaculis facilisis massa Etiam</q>
    <div class="author">By Author Name</div>
  </div>
  <div class="review" style="left:55px; top:982px">
    <q>Aam est nunc venenatis in tristique eu imperdiet ac nisl Cum sociis natoque penatibus et magnis dis parturient montes nascetur</q>
    <div class="author">By Author Name</div>
  </div>
  <div class="review" style="left:293px; top:978px">
    <q>Est nunc venenatis in tristique eu imperdiet ac nisl Cum sociis natoque penatibus et magnis dis parturient montes nascetur</q>
    <div class="author">By Author Name</div>
  </div>

  <h2 class="portfolio-title">Our Portfolio</h2>
  <div class="thumb" style="left:552px; top:864px; background:linear-gradient(135deg,#4a4a4a,#9a9a9a 55%,#e4e4e4)" role="img" aria-label="Photo of a modern bathroom with dark tiles and vanity"></div>
  <div class="thumb" style="left:664px; top:864px; background:linear-gradient(135deg,#6a2a14,#b45a2a 50%,#d8b48a)" role="img" aria-label="Photo of a kitchen with warm wood cabinets"></div>
  <div class="thumb" style="left:775px; top:864px; background:linear-gradient(135deg,#e8e6e0,#c9b08a 60%,#f2f0ea)" role="img" aria-label="Photo of a white kitchen with wooden island"></div>
  <div class="thumb" style="left:552px; top:960px; background:linear-gradient(135deg,#a9c6d6,#e6eef2 55%,#ffffff)" role="img" aria-label="Photo of a bright bathroom with freestanding tub and sea view"></div>
  <div class="thumb" style="left:664px; top:960px; background:linear-gradient(135deg,#5a3a26,#b88a60 55%,#e0c4a0)" role="img" aria-label="Photo of a warm toned bathroom with tub"></div>
  <div class="thumb" style="left:775px; top:960px; background:linear-gradient(135deg,#f4f4f2,#c8c8c4 55%,#5a5a58)" role="img" aria-label="Photo of a white kitchen with stainless range"></div>

  <footer class="footer">
    <div class="footer-links">
      <a href="#">HOME</a><span class="bar">|</span><a href="#">ABOUT US</a><span class="bar">|</span><a href="#">SERVICES</a><span class="bar">|</span><a href="#">TESIMONIALS</a><span class="bar">|</span><a href="#">PORTFOLIO</a><span class="bar">|</span><a href="#">SUPPORT</a><span class="bar">|</span><a href="#">CONTACT</a>
    </div>
    <div class="copyright">© Copyrights 2015 Meridale Real Estate. All Right Reserved</div>
    <div class="social" aria-label="Social links">
      <span></span><span></span><span></span>
    </div>
  </footer>

</div>
</body>
</html>
```